Heron Loan Partners Business Card

We need a business card design for our mortgage servicing company. In addition to servicing the loans of homeowners, we help homeowners with purchasing their homes and any mortgage refinancing. We would like to see designs that use the colors in the logo attached below (gold-ish yellow and navy blue), and any other design you deem fit! The design should communicate a simpler life with smart mortgages provided by Heron.

```html
<!DOCTYPE html>
<html lang="en">
<head>
<meta charset="utf-8">
<title>Heron Loan Partners Business Card</title>
<link href="https://fonts.googleapis.com/css2?family=Montserrat:wght@400;500;700;800&display=swap" rel="stylesheet">
<style>
  :root {
    --navy: #25204f;
    --gold: #e0ae35;
    --white: #ffffff;
    --ink: #1d1a33;
    --backdrop: #e9e9ec;
  }
  * { box-sizing: border-box; margin: 0; padding: 0; }
  html, body { width: 1200px; height: 880px; overflow: hidden; }
  body {
    background: var(--backdrop);
    font-family: "Montserrat", Arial, sans-serif;
    display: flex;
    flex-direction: column;
    align-items: center;
    justify-content: center;
    gap: 32px;
  }
  .card {
    position: relative;
    width: 700px;
    height: 400px;
    overflow: hidden;
    box-shadow: 0 6px 18px rgba(0,0,0,.18);
  }
  .card-front {
    background: var(--navy);
    display: flex;
    align-items: center;
    justify-content: center;
  }
  .brand-name {
    color: var(--gold);
    font-weight: 700;
    font-size: 46px;
    letter-spacing: .5px;
  }
  .card-back { background: var(--white); }
  .wave { position: absolute; inset: 0; width: 100%; height: 100%; }
  .back-brand {
    position: absolute;
    left: 56px;
    top: 170px;
    font-size: 24px;
  }
  .divider {
    position: absolute;
    left: 372px;
    top: 72px;
    width: 2px;
    height: 120px;
    background: var(--gold);
  }
  .contact {
    position: absolute;
    left: 396px;
    top: 50px;
    color: var(--ink);
  }
  .person-name {
    font-weight: 800;
    font-size: 19px;
    letter-spacing: .3px;
    color: var(--navy);
  }
  .person-name .surname { color: var(--gold); }
  .person-role { font-size: 14px; margin-top: 2px; }
  .contact-list { list-style: none; margin-top: 16px; }
  .contact-list li {
    display: flex;
    align-items: center;
    gap: 10px;
    font-size: 14px;
    margin-bottom: 8px;
  }
  .contact-list svg { width: 15px; height: 15px; flex: none; }
</style>
</head>
<body>

<section class="card card-front">
  <div class="brand-name">Heron Loan Partners</div>
</section>

<section class="card card-back">
  <svg class="wave" viewBox="0 0 700 400" preserveAspectRatio="none" aria-hidden="true">
    <path d="M0,400 L0,392 C120,320 300,330 450,290 C580,255 650,190 700,150 L700,400 Z" fill="var(--navy)"/>
    <path d="M0,382 C120,310 300,320 450,280 C580,245 650,180 700,140" fill="none" stroke="var(--gold)" stroke-width="5"/>
  </svg>

  <div class="brand-name back-brand">Heron Loan Partners</div>

  <div class="divider"></div>

  <div class="contact">
    <div class="person-name">DANA <span class="surname">WHITFIELD</span></div>
    <div class="person-role">Owner</div>
    <ul class="contact-list">
      <li>
        <svg viewBox="0 0 16 16"><path d="M2 5c0-2 3-3 6-3s6 1 6 3v1h-3V5H5v1H2z M4 7h8l1 6H3z" fill="var(--gold)"/></svg>
        555.014.2290
      </li>
      <li>
        <svg viewBox="0 0 16 16"><rect x="1" y="3" width="14" height="10" fill="var(--gold)"/><path d="M1 3l7 6 7-6" fill="none" stroke="var(--white)" stroke-width="1.4"/></svg>
        info@heronloanpartners.com
      </li>
      <li>
        <svg viewBox="0 0 16 16"><circle cx="8" cy="8" r="7" fill="var(--gold)"/><path d="M1 8h14 M8 1c-3 3-3 11 0 14 M8 1c3 3 3 11 0 14" fill="none" stroke="var(--white)" stroke-width="1"/></svg>
        www.heronloanpartners.com
      </li>
    </ul>
  </div>
</section>

</body>
</html>
```